BOLD & MINIMALIST DESIGN NEEDED

We want a very bold but minimalistic business card design that is impactful and utilizes both sides of the business card. Our current logo is included for your use.

We want bold fonts and good use of negative space. We don't want the logo to overpower the design.

Target Market(s)

Professionals who are building new commercial buildings.

Industry/Entity Type

Construction

Contact Information for Business Card

Name, Title, email, office phone, cell phone, website

Font styles to use
Serif
Sans Serif

Requirements
Must have
• Bold design!

```html
<!DOCTYPE html>
<html lang="en">
<head>
<meta charset="utf-8">
<title>Ridgeway Design + Build — Stationery</title>
<link href="https://fonts.googleapis.com/css2?family=Montserrat:wght@400;500;700&family=Lato:wght@400&display=swap" rel="stylesheet">
<style>
  :root{
    --backdrop:#e9e4de;
    --paper:#ffffff;
    --ink:#111111;
    --text:#3a3a3a;
    --muted:#5a5a5a;
    --green:#7cc242;
  }
  *{box-sizing:border-box;margin:0;padding:0}
  html,body{width:1200px;height:1067px;overflow:hidden}
  body{background:var(--backdrop);font-family:'Montserrat',sans-serif;color:var(--text);position:relative}

  .card{position:absolute;background:var(--paper);border-radius:18px;box-shadow:0 3px 10px rgba(0,0,0,.15)}
  .card--front{left:74px;top:250px;width:468px;height:267px;display:flex;align-items:center;justify-content:center}
  .card--back{left:77px;top:546px;width:463px;height:264px}

  .brand{display:flex;align-items:center;color:var(--ink);font-family:'Montserrat',sans-serif;font-weight:700;line-height:1.15}
  .brand__mark{flex:none;background:var(--green)}
  .card--front .brand{font-size:30px;gap:14px}
  .card--front .brand__mark{width:22px;height:22px}
  .card--back .brand{position:absolute;left:28px;top:108px;width:200px;font-size:18px;gap:10px}
  .card--back .brand__mark{width:14px;height:14px}
  .lh .brand{position:absolute;left:52px;top:72px;font-size:15px;gap:8px}
  .lh .brand__mark{width:11px;height:11px}

  .card__divider{position:absolute;left:247px;top:52px;width:2px;height:161px;background:var(--green)}
  .card__details{position:absolute;left:266px;top:48px;color:var(--text)}
  .card__name{font-size:20px;font-weight:700;color:var(--green);letter-spacing:.5px}
  .card__title{font-size:12.5px;font-weight:500;margin-top:3px;letter-spacing:.5px}
  .card__address{font-size:12.5px;line-height:18.5px;margin-top:10px}
  .contact{list-style:none}
  .card .contact{margin-top:8px;font-size:12.5px}
  .card .contact li{height:18.5px;display:flex;align-items:center;gap:6px}
  .contact svg{width:9px;height:9px;fill:var(--green);flex:none}

  .lh{position:absolute;left:573px;top:143px;width:551px;height:780px;background:var(--paper);box-shadow:0 3px 12px rgba(0,0,0,.15)}
  .lh__divider{position:absolute;left:362px;top:34px;width:1.5px;height:84px;background:var(--green)}
  .lh__contact{position:absolute;left:375px;top:33px;font-size:10px;color:var(--text)}
  .lh__address{line-height:14px}
  .lh .contact{margin-top:4px}
  .lh .contact li{height:14px;display:flex;align-items:center;gap:5px}
  .lh .contact svg{width:7px;height:7px}
  .lh__recipient{position:absolute;left:52px;top:183px;font-family:'Lato',sans-serif;color:var(--muted)}
  .lh__recipient-name{font-size:10.5px;letter-spacing:.2px}
  .lh__recipient small{display:block;font-size:8px;line-height:13.5px;margin-top:2px}
  .lh__body{position:absolute;left:52px;top:276px;width:447px;font-family:'Lato',sans-serif;font-size:8px;line-height:13.5px;color:var(--muted);text-align:justify}
  .lh__body p+p{margin-top:12px}
  .lh__closing{position:absolute;left:52px;top:578px;font-family:'Lato',sans-serif;color:var(--muted)}
  .lh__closing p{font-size:8.5px}
  .lh__signer{margin-top:34px;font-size:10.5px}
</style>
</head>
<body>

<section class="card card--front">
  <div class="brand"><span class="brand__mark"></span><span class="brand__name">Ridgeway Design + Build</span></div>
</section>

<section class="card card--back">
  <div class="brand"><span class="brand__mark"></span><span class="brand__name">Ridgeway<br>Design + Build</span></div>
  <div class="card__divider"></div>
  <div class="card__details">
    <h2 class="card__name">DANIEL REYES</h2>
    <p class="card__title">OWNER-CEO</p>
    <p class="card__address">Your address, City<br>State, Zip 1234</p>
    <ul class="contact">
      <li><svg viewBox="0 0 10 10"><path d="M1 4h8l-1 4H2z M2 2h6v2H2z"/></svg>123 456 789</li>
      <li><svg viewBox="0 0 10 10"><path d="M3 0h4a1 1 0 0 1 1 1v8a1 1 0 0 1-1 1H3a1 1 0 0 1-1-1V1a1 1 0 0 1 1-1zm0 1.5v6h4v-6z"/></svg>123 456 789</li>
      <li><svg viewBox="0 0 10 10"><path d="M0 2h10v6H0z"/></svg>info@ridgewaybuild.com</li>
      <li><svg viewBox="0 0 10 10"><circle cx="5" cy="5" r="5"/></svg>www.ridgewaybuild.com</li>
    </ul>
  </div>
</section>

<article class="lh">
  <div class="brand"><span class="brand__mark"></span><span class="brand__name">Ridgeway<br>Design + Build</span></div>
  <div class="lh__divider"></div>
  <div class="lh__contact">
    <p class="lh__address">Your address, City<br>State, Zip 1234</p>
    <ul class="contact">
      <li><svg viewBox="0 0 10 10"><path d="M1 4h8l-1 4H2z M2 2h6v2H2z"/></svg>123 456 789</li>
      <li><svg viewBox="0 0 10 10"><path d="M3 0h4a1 1 0 0 1 1 1v8a1 1 0 0 1-1 1H3a1 1 0 0 1-1-1V1a1 1 0 0 1 1-1zm0 1.5v6h4v-6z"/></svg>123 456 789</li>
      <li><svg viewBox="0 0 10 10"><path d="M0 2h10v6H0z"/></svg>info@ridgewaybuild.com</li>
      <li><svg viewBox="0 0 10 10"><circle cx="5" cy="5" r="5"/></svg>www.ridgewaybuild.com</li>
    </ul>
  </div>

  <div class="lh__recipient">
    <p class="lh__recipient-name">MARA WHITFIELD</p>
    <small>Chief Executive Officer<br>City/State, Zip Code</small>
  </div>

  <div class="lh__body">
    <p>Proin gravida nibh vel velit auctor aliquet. Aenean sollicitudin, lorem quis bibendum auctor, nisi elit consequat ipsum, nec sagittis sem nibh id elit. Duis sed odio sit amet nibh vulputate cursus a sit amet mauris. Morbi accumsan ipsum velit. Nam nec tellus a odio tincidunt auctor a ornare odio. Sed non mauris vitae erat consequat auctor eu in elit. Class aptent taciti sociosqu ad litora torquent ugue. Sed non neque elit. Sed ut imperdiet nisi. Proin condimentum fermentum nunc. Etiam pharetra, imperdiet nisi. Proin condimentum fermentum nunc. Etiam pharetra, erat sed fermentum feugiat, velit mauris egestas quam, ut aliquam massa nisl quis neque. Suspendisse in orci enim.</p>
    <p>This is a sample version of Lorem Ipsum. Proin gravida nibh vel velit auctor aliquet. Aenean sollicitudin, lorem quis bibendum auctor, nisi elit consequat ipsum, nec sagittis sem nibh id elit. Duis sed odio sit amet nibh vulputate cursus a sit amet mauris. Morbi accumsan ipsum velit. Nam nec tellus a odio tincidunt auctor a ornare odio. Sed non mauris vitae erat consequat auctor eu in elit. Class aptent consequat auctor eu in elit. Class aptent taciti sociosqu ad litora torquent per conubia nostra, per inceptos himenaeos. Mauris in erat justo.</p>
    <p>Nullam ac urna eu felis dapibus condimentum sit amet a augue. Sed non neque elit. Sed ut imperdiet nisi. Proin condimentum fermentum nunc. Etiam pharetra, erat sed fermentum feugiat, velit mauris egestas quam.Nullam ac urna eu felis dapibus condimentum sit amet a aug pharetra, erat sed fermentum feugiat, velit mauris egestas quam.Nullam ac urna eu felis dapibus condimentum sit amet a augue. Sed non neque elit. Sed ut imperdiet nisi. Proin condimentum fermentum nunc.</p>
  </div>

  <div class="lh__closing">
    <p>Sincerely,</p>
    <p class="lh__signer">Owen Calder</p>
  </div>
</article>

</body>
</html>
```